TALVORE GROUP OF CLINICS

We need a medical & lab report file. The design should be healthcare related. Our current file design has been used for almost 10 years. We need something more fresh & up-to-date. We have attached the current file design.

Need extra days to review

```html
<!DOCTYPE html>
<html lang="en">
<head>
<meta charset="utf-8">
<title>Talvore Group of Clinics – Medical Report File</title>
<link rel="stylesheet" href="https://fonts.googleapis.com/css2?family=Open+Sans:wght@400;600;700;800&family=Fredoka:wght@500&display=swap">
<style>
  :root{
    --navy:#1f4f86;
    --navy-deep:#183f70;
    --ink:#33318a;
    --sky:#4bbdf0;
    --sky-deep:#2e9fdc;
    --cyan-text:#1fb3ea;
    --row-text:#1a2d68;
    --white:#ffffff;
    --paper:#f4f6f8;
  }
  *{box-sizing:border-box;margin:0;padding:0}
  html,body{width:1200px;height:847px;overflow:hidden;background:var(--paper)}
  .folder{position:relative;width:1200px;height:847px;display:flex;font-family:"Open Sans",Arial,sans-serif}

  /* Back panel: clinic directory */
  .directory{position:relative;width:600px;height:847px;background:var(--navy);overflow:hidden}
  .edge-top,.edge-bottom{position:absolute;left:0;width:100%;background:var(--sky-deep)}
  .edge-top{top:0;height:14px}
  .edge-bottom{bottom:0;height:22px}
  .directory-title{position:absolute;left:90px;top:40px;height:54px;padding:0 30px;background:var(--white);border-radius:27px;
    display:flex;align-items:center;font-weight:800;font-size:26px;color:var(--ink);letter-spacing:.3px}
  .clinic-list{position:absolute;left:22px;top:116px;list-style:none}
  .clinic{position:relative;width:556px;height:80px;margin-bottom:16px}
  .clinic-card{position:absolute;left:60px;top:0;width:496px;height:80px;background:var(--sky);border-radius:40px}
  .clinic-card::after{content:"";position:absolute;inset:5px;border:1.5px dashed var(--white);border-radius:35px}
  .clinic-body{position:absolute;left:62px;top:8px;right:30px;z-index:1}
  .clinic-name{font-weight:700;font-size:11.5px;color:var(--white);text-transform:uppercase;letter-spacing:.2px;line-height:15px}
  .clinic-line{font-size:9.6px;color:var(--row-text);line-height:13px;white-space:nowrap}
  .clinic-badge{position:absolute;left:0;top:-2px;width:84px;height:84px;border-radius:50%;background:var(--white);
    display:flex;align-items:center;justify-content:center;z-index:2}
  .clinic-badge::after{content:"";position:absolute;inset:4px;border:1.5px dashed var(--sky);border-radius:50%}
  .badge-name{font-weight:800;font-size:11px;color:var(--ink);letter-spacing:.3px}

  /* Front cover */
  .cover{position:relative;width:600px;height:847px;background:var(--white);overflow:hidden}
  .cover-art{position:absolute;inset:0}
  .tagline{position:absolute;left:80px;top:34px;font-family:"Fredoka",sans-serif;font-weight:500;font-size:24px;line-height:30px;color:var(--cyan-text)}
  .tagline-mark{position:absolute;left:38px;top:40px}
  .cover-title{position:absolute;left:48px;top:300px;height:62px;padding:0 22px;background:var(--white);border-radius:14px;
    display:flex;align-items:center;font-weight:800;font-size:38px;color:var(--ink);letter-spacing:-.3px}
  .brand{position:absolute;left:370px;top:640px;display:flex;align-items:center;gap:12px}
  .brand-dot{width:22px;height:22px;border-radius:50%;background:var(--sky)}
  .brand-name{font-weight:700;font-size:24px;color:var(--ink);letter-spacing:.3px}
</style>
</head>
<body>
<main class="folder">

  <section class="directory" aria-label="Clinic directory">
    <div class="edge-top"></div>
    <h2 class="directory-title">TALVORE GROUP OF CLINICS</h2>
    <ul class="clinic-list">
      <li class="clinic">
        <div class="clinic-badge"><span class="badge-name">TALVORE</span></div>
        <div class="clinic-card"><div class="clinic-body">
          <p class="clinic-name">Pusat Perubatan Talvore</p>
          <p class="clinic-line">Level 12, Orchid Annexe, No. 4, Jalan Seri Kenanga,</p>
          <p class="clinic-line">50480 Kuala Lumpur</p>
          <p class="clinic-line">Tel. No: +603-5550-1100 Fax No: +603-5550-1101</p>
          <p class="clinic-line">Email: pusat@talvoreclinic.example</p>
        </div></div>
      </li>
      <li class="clinic">
        <div class="clinic-badge"><span class="badge-name">TALVORE</span></div>
        <div class="clinic-card"><div class="clinic-body">
          <p class="clinic-name">Klinik Talvore (Bukit Cendana)</p>
          <p class="clinic-line">No. 8, Jalan Cendana 2/4, Bukit Cendana,</p>
          <p class="clinic-line">40160 Selangor Darul Ehsan</p>
          <p class="clinic-line">Tel. No: +603-5550-2200 Fax No: +603-5550-2201</p>
          <p class="clinic-line">Email: cendana@talvoreclinic.example</p>
        </div></div>
      </li>
      <li class="clinic">
        <div class="clinic-badge"><span class="badge-name">TALVORE</span></div>
        <div class="clinic-card"><div class="clinic-body">
          <p class="clinic-name">Klinik Talvore (Teluk Seri)</p>
          <p class="clinic-line">Lot 2A-1-1, 2A-1-2, Persiaran Teluk Seri, 11920 Penang</p>
          <p class="clinic-line">Tel. No: +604-555-3300 Fax No: +604-555-3301</p>
          <p class="clinic-line">Email: telukseri@talvoreclinic.example</p>
        </div></div>
      </li>
      <li class="clinic">
        <div class="clinic-badge"><span class="badge-name">TALVORE</span></div>
        <div class="clinic-card"><div class="clinic-body">
          <p class="clinic-name">Klinik Talvore (Sri Melati)</p>
          <p class="clinic-line">No. 52, Jalan Pusat Niaga Sri Melati 1/2, Pusat Niaga Sri Melati</p>
          <p class="clinic-line">71960 Bandar Sri Melati, Negeri Sembilan</p>
          <p class="clinic-line">Tel. No: +606-555-4400 Fax No: +606-555-4401</p>
          <p class="clinic-line">Email: srimelati@talvoreclinic.example</p>
        </div></div>
      </li>
      <li class="clinic">
        <div class="clinic-badge"><span class="badge-name">TALVORE</span></div>
        <div class="clinic-card"><div class="clinic-body">
          <p class="clinic-name">Talvore Medical Clinic (Terminal A)</p>
          <p class="clinic-line">Lot A12, Arrival Level, Main Terminal Building,</p>
          <p class="clinic-line">Terminal A, 64010 Selangor Darul Ehsan</p>
          <p class="clinic-line">Tel. No: +603-5550-5500 Fax No: +603-5550-5501</p>
          <p class="clinic-line">Email: terminala@talvoreclinic.example</p>
        </div></div>
      </li>
      <li class="clinic">
        <div class="clinic-badge"><span class="badge-name">TALVORE</span></div>
        <div class="clinic-card"><div class="clinic-body">
          <p class="clinic-name">Talvore Medical Clinic (Terminal B)</p>
          <p class="clinic-line">B3-1-07, Landside Arrival Level,</p>
          <p class="clinic-line">Terminal B, 64010 Selangor Darul Ehsan</p>
          <p class="clinic-line">Tel. No: +603-5550-6600 Fax No: +603-5550-6601</p>
          <p class="clinic-line">Email: terminalb@talvoreclinic.example</p>
        </div></div>
      </li>
      <li class="clinic">
        <div class="clinic-badge"><span class="badge-name">TALVORE</span></div>
        <div class="clinic-card"><div class="clinic-body">
          <p class="clinic-name">Talvore Medical Clinic (North Airport)</p>
          <p class="clinic-line">Unit 1-04, Level 1, Passenger Terminal Building,</p>
          <p class="clinic-line">North Airport, 11930 Penang</p>
          <p class="clinic-line">Tel. No: +604-555-7700 Fax No: +604-555-7701</p>
          <p class="clinic-line">Email: northair@talvoreclinic.example</p>
        </div></div>
      </li>
    </ul>
    <div class="edge-bottom"></div>
  </section>

  <section class="cover" aria-label="Front cover">
    <svg class="cover-art" width="600" height="847" viewBox="0 0 600 847">
      <defs>
        <linearGradient id="anatomyTone" x1="0" y1="0" x2="1" y2="1">
          <stop offset="0" stop-color="#0d3a7a"/>
          <stop offset=".5" stop-color="#1d7fd0"/>
          <stop offset="1" stop-color="#0b2f66"/>
        </linearGradient>
        <linearGradient id="hexTone" x1="0" y1="0" x2="1" y2="1">
          <stop offset="0" stop-color="#1a5fb8"/>
          <stop offset="1" stop-color="#082a5e"/>
        </linearGradient>
      </defs>
      <rect x="0" y="0" width="600" height="14" fill="#2e9fdc"/>
      <polygon points="0,250 470,14 600,14 600,300 0,640" fill="url(#anatomyTone)" role="img" aria-label="Illustration of human lungs and heart in blue x-ray style"/>
      <polygon points="0,640 600,300 600,345 0,700" fill="#4bbdf0"/>
      <polygon points="0,700 600,345 600,362 210,825 0,825" fill="#1f4f86"/>
      <g stroke="#ffffff" stroke-width="4">
        <polygon points="540,220 575,240 575,280 540,300 505,280 505,240" fill="url(#hexTone)" role="img" aria-label="Brain scan illustration"/>
        <polygon points="450,265 490,288 490,334 450,357 410,334 410,288" fill="url(#hexTone)" role="img" aria-label="Rib cage illustration"/>
        <polygon points="190,450 230,473 230,519 190,542 150,519 150,473" fill="url(#hexTone)" role="img" aria-label="Kidneys illustration"/>
        <polygon points="115,505 155,528 155,574 115,597 75,574 75,528" fill="url(#hexTone)" role="img" aria-label="Heart illustration"/>
      </g>
      <rect x="0" y="825" width="600" height="22" fill="#2e9fdc"/>
    </svg>
    <svg class="tagline-mark" width="26" height="22" viewBox="0 0 26 22"><polygon points="0,0 26,11 0,22" fill="#1f4f86"/></svg>
    <p class="tagline">“Your<br>Healthcare<br>Partner”</p>
    <h1 class="cover-title">MEDICAL REPORT</h1>
    <div class="brand">
      <span class="brand-dot"></span>
      <span class="brand-name">TALVORE GROUP</span>
    </div>
  </section>

</main>
</body>
</html>
```